Paint Retail Store needs a logo/label redesign.

We are redesigning a label for one of our products. We are a paint retail store that specializes on selling premium paint at outlet prices called Coat & Gleam. We want the redesign to exude professionalism and cleanliness. Attached is a picture of our current label. We want the logo Coat & Gleam to be modified to a more modern feel that still incorporates the iconic paint roller element that has been part of our brand identity. We want the description of: Exceptional Durability/ Luxurious Finish to be included in the front of the label to attract our clients. Include all of the information and description of the current label to the new label. Attached are pictures of our competitors labels so you have an idea of what we are looking for. We also want the background of the label to be a clean solid color.

Target Market(s)

Home Owners, DIY enthusiasts, Contractors/painters, interior designers

Industry/Entity Type

Paint and Coatings retail store

Colors

Designer to choose colors to be used in the design.

Requirements
Must have
• Semigloss Finish, Exceptional Durability, Luxurios Finish. Include all the information that are on the side of the current label to the new label. Include the phrase: Made in the US.
Nice to have
• A redesign of the logo: Coat & Gleam to convey a more modern/professional look.
Should not have
• Feminine colors.

```html
<!DOCTYPE html>
<html lang="en">
<head>
<meta charset="utf-8">
<title>Coat &amp; Gleam Semi-Gloss Latex Paint Label</title>
<link href="https://fonts.googleapis.com/css2?family=Poppins:wght@400;500;600;800&family=Oswald:wght@300;400&family=Cinzel:wght@500&family=Baloo+2:wght@800&display=swap" rel="stylesheet">
<style>
  :root {
    --navy-deep: #0a1b36;
    --navy: #12336b;
    --navy-panel: #0c3b78;
    --ink-box: #0b2140;
    --orange: #f28a1f;
    --orange-dark: #e2601f;
    --gold: #c9a24a;
    --white: #ffffff;
  }
  * { margin: 0; padding: 0; box-sizing: border-box; }
  html, body { width: 1200px; height: 870px; overflow: hidden; }
  body {
    position: relative;
    background: linear-gradient(180deg, var(--navy-deep) 0%, var(--navy) 60%, #173d7c 100%);
    color: var(--white);
    font-family: "Poppins", sans-serif;
  }
  .abs { position: absolute; }

  /* Left instruction column */
  .directions {
    left: 49px; top: 62px; width: 284px;
    font-size: 11.3px; line-height: 14.5px; font-weight: 500;
    text-align: justify; letter-spacing: -0.1px;
  }
  .ingredients {
    left: 63px; top: 655px; width: 256px; height: 172px;
    background: var(--ink-box); border-radius: 10px;
    padding: 12px 24px 0 24px;
  }
  .ingredients h3 {
    font-size: 16px; font-weight: 500; word-spacing: 8px;
    border-bottom: 2px solid var(--white); padding-bottom: 6px; margin-bottom: 10px;
  }
  .ingredients ul { list-style: none; font-size: 11px; line-height: 14.5px; }
  .ingredients li { display: flex; }
  .ingredients li .dots { flex: 1; border-bottom: 1px dotted var(--white); margin: 0 1px 4px; }
  .ingredients .note { font-size: 11px; margin-top: 14px; }

  /* Centre front panel */
  .finish-bar {
    left: 455px; top: 34px; width: 289px; height: 47px;
    background: var(--orange); text-align: center;
    font-size: 28px; font-weight: 800; line-height: 47px; letter-spacing: 1px;
  }
  .brand { left: 458px; top: 118px; width: 280px; text-align: center; }
  .brand-name {
    font-size: 46px; font-weight: 800; line-height: 50px; color: var(--white);
    display: flex; align-items: center; justify-content: center; gap: 10px; flex-direction: column;
  }
  .brand-mark { width: 56px; height: 56px; border-radius: 50%; background: var(--orange); }
  .tagline {
    left: 470px; top: 314px; width: 280px; text-align: center;
    font-family: "Oswald", sans-serif; font-weight: 300; font-size: 21px;
  }
  .grade {
    left: 480px; top: 388px; width: 240px; text-align: center;
    font-family: "Cinzel", serif; color: var(--gold); font-size: 26px;
    border-top: 1px solid var(--gold); border-bottom: 1px solid var(--gold); line-height: 32px;
  }
  .claim {
    left: 400px; width: 400px; text-align: center;
    font-family: "Oswald", sans-serif; font-weight: 300; font-size: 34px; line-height: 40px;
  }
  .claim-one { top: 430px; }
  .claim-rule { left: 530px; top: 470px; width: 140px; height: 3px; background: var(--orange); }
  .claim-two { top: 473px; }
  .hero-art {
    left: 412px; top: 540px; width: 398px; height: 250px;
    background: linear-gradient(160deg, var(--orange) 40%, var(--orange-dark));
    border-radius: 20px 40px 30px 60px;
  }
  .product-name {
    left: 395px; top: 580px; width: 410px; text-align: center;
    font-family: "Baloo 2", sans-serif; font-weight: 800; font-size: 78px; line-height: 80px;
  }
  .product-use {
    left: 395px; top: 668px; width: 410px; text-align: center;
    font-size: 26px; font-weight: 800; letter-spacing: 0.5px;
  }
  .frozen-badge {
    left: 560px; top: 738px; width: 80px; height: 80px; border-radius: 50%;
    background: #2a9be0; border: 5px solid var(--white);
  }
  .volume {
    left: 351px; top: 778px;
    font-family: "Oswald", sans-serif; font-weight: 300; font-size: 19px; line-height: 28px;
  }
  .origin { left: 745px; top: 818px; font-family: "Oswald", sans-serif; font-weight: 300; font-size: 13px; }

  /* Right safety column */
  .safety { left: 863px; width: 284px; font-size: 11px; line-height: 14.5px; }
  .alert { color: var(--orange); }
  .head-alert { top: 62px; font-weight: 600; font-size: 11.2px; }
  .caution { top: 92px; }
  .steps-panel {
    left: 863px; top: 154px; width: 283px; height: 177px;
    background: var(--navy-panel);
  }
  .steps-title {
    position: absolute; left: 32px; top: -4px; width: 218px; height: 20px;
    background: var(--orange); font-size: 11px; font-weight: 600; text-align: center; line-height: 20px;
  }
  .step { position: absolute; width: 90px; font-size: 7px; line-height: 9px; }
  .step .pict { width: 49px; height: 49px; background: var(--white); border: 2px solid #111; margin-bottom: 4px;
    background: linear-gradient(135deg, #fff 45%, #111 45%); }
  .steps-divider { position: absolute; left: 16px; right: 16px; top: 92px; height: 1px; background: var(--white); }
  .ventilation { top: 338px; text-align: justify; }
  .ventilation .lead { letter-spacing: 1.6px; }
  .first-aid { top: 555px; }
  .delayed { top: 627px; }
  .warning { top: 714px; }
  .keep-away { top: 772px; }
</style>
</head>
<body>

  <section class="abs directions">
    <p>Where To Use: Walls cabinets, cellings, trim and doors. Use over drywall, wood, concrete/brick plaster and wallpaper. See bellow for preparation steps:</p>
    <p>How Much You Need: For one coat coverage, apply at a maximum of 400 square feet per gallon. Rough or textured surfaces may require more allow for 125-300 square feet per gallon. Do not thin.</p>
    <p>What Tools To Use: May be applied with a quality roller, a nylon/polyester brush, or a paint pad How To Apply Room and surface temperature must be 50 degrees Fahrenheit. Allow at least 4 hours of drying time before recoating. Mix gallons togheter for color and sheen uniformity when using more than one gallon of the same product</p>
    <p>Care for Freshly Painted Surfaces. Freshly painted surfaced may be washed either 30 days- Until then avoid touching, wiping, or wetting the surface. Then clean with mild, non-abrasive, non-oily cleanser and water. Do not place objects on painted sirfaces untill throughly dry. Soap and Water Cleanup</p>
    <p>HOW TO PREPARE THE SURFACE</p>
    <p>Previously Painted Surfaces: Remove loose paint, Wash with a mild, non-abrasive, non-oily cleanser and water. Rinse completely, let dry Patch holes and cracks with speckling paste and let dry. Sand patched area and wipe off residue. Send all smooth or glossy surfaces, nnse well. Unpainted Surfaces: Wallboard or brywall Concrete/brick Allow new masonry to sure at least 30 days Etch smooth unpainted concrete. Remove all loose concrete and efflorescence: Rinse and allow to dry Plaster (new) Must be died and cured for 30 days. Prime with primer. Let dry 4 hours before top coating. Wallpaper Vinyl coated wallpaper may be coated if all seams and edges are glued tight, Self-sand and wipe clean. Use primer and alllow 24 hours to dry.</p>
  </section>

  <section class="abs ingredients">
    <h3>CAS NO. INGREDIENTS</h3>
    <ul>
      <li>7732-18-5<span class="dots"></span>Water</li>
      <li>Propietary<span class="dots"></span>Vinyl Polymer</li>
      <li>13463-67-7<span class="dots"></span>Titanium Dioxide</li>
      <li>Proprietary<span class="dots"></span>Acrylic Polymer</li>
      <li>471-34-1<span class="dots"></span>Calcium Carbonate</li>
      <li>14464-46-1<span class="dots"></span>Cristobalite</li>
    </ul>
    <p class="note">NON-PHOTOCHEMICALLY REACTIVE</p>
  </section>

  <div class="abs finish-bar">SEMI - GLOSS</div>

  <div class="abs brand">
    <div class="brand-name"><span class="brand-mark"></span><span>Coat &amp; Gleam</span></div>
  </div>
  <div class="abs tagline">Premium Paint at Outlet Prices</div>

  <div class="abs grade">Premium Grade</div>
  <div class="abs claim claim-one">EXCEPTIONAL DURABILITY</div>
  <div class="abs claim-rule"></div>
  <div class="abs claim claim-two">LUXURIOUS FINISH</div>

  <div class="abs hero-art" role="img" aria-label="Orange brush strokes with a paint roller illustration"></div>
  <div class="abs product-name">Latex Paint</div>
  <div class="abs product-use">INTERIOR / EXTERIOR</div>
  <div class="abs frozen-badge" role="img" aria-label="Frozen product badge"></div>

  <div class="abs volume">1 Gal.<br>(124 OZ/3.667 Lts.)</div>
  <div class="abs origin">Made in the US.</div>

  <p class="abs safety alert head-alert">SOLID VINYL WALLPAPER CANNOT BE PAINTED</p>
  <p class="abs safety caution">CAUTIONS CONTAINS CRYSTALLINE SILICA- Use Cleanup: Clean tools, spills and splatters immediately with soap and water.</p>

  <section class="abs steps-panel">
    <div class="steps-title">KEEP FROM FREEZING-DO NOT THIN</div>
    <div class="step" style="left:16px;top:18px"><div class="pict" role="img" aria-label="Hand pictogram"></div>Clean, dull and dry surface</div>
    <div class="step" style="left:117px;top:18px"><div class="pict" role="img" aria-label="Stirring pictogram"></div>Stir paint thoroughly</div>
    <div class="step" style="left:218px;top:18px"><div class="pict" role="img" aria-label="Brush at ceiling pictogram"></div>Start at ceiling edge</div>
    <div class="steps-divider"></div>
    <div class="step" style="left:16px;top:100px"><div class="pict" role="img" aria-label="Roller pictogram"></div>Paint "N" pattern-fill in</div>
    <div class="step" style="left:117px;top:100px"><div class="pict" role="img" aria-label="Trim brush pictogram"></div>Paint trim last</div>
    <div class="step" style="left:218px;top:100px"><div class="pict" role="img" aria-label="Washing pictogram"></div>Soap and water clean up</div>
  </section>

  <p class="abs safety ventilation"><span class="lead">only with adecuate ventilation To avoid</span> overexposure, open windows and doors or use other means to ensure fresh air entry during aplication and drying. If you experience eye watering, headaches, or dizzyness, increase fresh air, or wear respiratory protection or leave the area. Adecuate ventilation required when sending or abrading the dried film. If adequate ventilation cannot ve provided wear an approved particulate respirator. Follow resporator manufacturer's directions for respirator use. Avoid contact with eyes and skin Wash hands after using. Keep container closed when not in use Do not transfer contents to other containers for storage</p>
  <p class="abs safety first-aid">FIRST AID. In case of eye contact flush thoroughly with large amounts of water. Get medical attention if mation persists, fallowed, call Poison Control Center. hospital emergency room, or physician immediately</p>
  <p class="abs safety delayed">DELAYED EFFECTS FROM LONG TERM OVEREXPOSURE Abrading on sanding of the dry film may release crystalino silica which has been shown to cause lung damage and cancer under long term expusurur</p>
  <p class="abs safety warning">WARNING: This product contains chemicals known to the State of California to cause cancer and birth defects or other reproductive ha</p>
  <p class="abs safety alert keep-away">DO NOT TAKE INTERNALLY<br>KEEP OUT OF THE REACH OF CHILDREN</p>

</body>
</html>
```